App-Design für Vergleichsportal für Reparaturen
Zielgruppe
Flickwerkzentrale ist das Vergleichsportal für Reparaturen in deiner Nähe. Egal ob du eine Werkstatt für dein Smartphone, Tablet, Laptop, Computer, Smartwatch oder Spielkonsole suchst. Mit uns findest du deine passende Reparaturwerkstat in deiner Nähe mit dem besten Preis für dich. Du kannst dich direkt über unser Portal deinen Reparaturauftrag erhalten und wirst durch unser Sicher Kaufen Käuferschutz und unser VORMANT Treuhandschutz abgesichert.
Aufgabenstellung
Unter Flickwerkzentrale.de kann das aktuelle Design angeschaut werden. Die Farbe sollten übernommen werden.
Über die Startseite kann der Kunde sein Gerät, Service sowie seine Adresse eingeben. Auf der Vergleichsseite bekommt der Kunde die Übersicht welche Reparaturwerkstätten es gibt, zu welche Preisen die ausgewählte Dienstleistung angeboten wird. Wenn der Kunde auf den Button 'Jetzt Online Bestpreis buchen' drückt, dann kommt der Kunde in den Warenkorb. Im Warenkorb können noch weitere Dienstleistungen und Produkte dazugebucht werden. Und anschließend kommt der Kunde in die Kasse und kann der Bestellvorgang beenden. Die Benutzerführung sollte einfach sein. Im Fokus steht die Vergleichsseite. Dort sollte der Kunde ca. 4 Werkstätten auf einen Blick sehen können. Könnte ausschauen wie bei Tarifblick in der Kategorie Mobilfunk.
Die Vergleichseite sollte auf jeden Fall folgende Elemente enthalten:
- Entfernung zur Werkstatt in Meter bzw. Kilometer
- Logo der Werkstatt
- Name der Werkstatt
- Bewertungssterne der Werkstatt
- Reparaturzeit und Ersatzeilverfügbarkeit
- Reparaturpreis (Platz sollte auch bei Auswahl von 2 Dienstleistungen vorhanden sein)
- Rabattanzeige
- Qualitätssiegel (noch nicht vorhanden)
- Anzeige von Verknappung (z. B. noch 3 Termin frei)
- Qualitätsmerkmale (z. B. 12 Monate Garantie)
Die Merkmale Öffnungszeiten, Adresse, Kostenpflichtige Zusatzleistungen können aus Platzgründen in den Warenkorbseite wandern außer es gibt eine schöne und einfache Lösung.
In der Warenkorbseite kann dazu auch die Tarifblick Seite dienen.
Bei allen sollte auf die Benutzerfreundlichkeit geachtet werden.
Bei offenen Frage stehe ich zur Verfügung und freue mich auf viele Designs.
Vielen DANK im Voraus!

```html
<!DOCTYPE html>
<html lang="de">
<head>
<meta charset="utf-8">
<title>Flickwerkzentrale – App Screens</title>
<link href="https://fonts.googleapis.com/css2?family=Roboto:wght@400;500;700&display=swap" rel="stylesheet">
<style>
:root{
  --green:#8cc63f;
  --navy:#234b5e;
  --ink:#1d1d1d;
  --muted:#8a8a8a;
  --line:#dcdcdc;
  --band:#efefef;
  --canvas:#f6f6f6;
  --white:#ffffff;
}
*{box-sizing:border-box;margin:0;padding:0}
html,body{width:1200px;height:961px;overflow:hidden}
body{background:var(--canvas);font-family:"Roboto",Helvetica,Arial,sans-serif;color:var(--ink);position:relative}
.screen{position:absolute;width:236px;height:421px;background:var(--white);box-shadow:0 1px 4px rgba(0,0,0,.18);overflow:hidden}
.abs{position:absolute}
.status{position:absolute;top:0;left:0;right:0;height:12px;font-size:6px;display:flex;justify-content:space-between;align-items:center;padding:0 4px}
.status .bat{display:inline-block;width:12px;height:5px;background:var(--ink);margin-left:2px;vertical-align:middle}
.back{position:absolute;left:8px;top:28px;width:6px;height:6px;border-left:1.4px solid var(--ink);border-bottom:1.4px solid var(--ink);transform:rotate(45deg)}
.basket{position:absolute;right:8px;top:25px}
.brand{position:absolute;top:23px;left:0;right:0;text-align:center;font-size:10px;font-weight:500;color:var(--navy)}
.brand::before{content:"";display:inline-block;width:7px;height:7px;border-radius:50%;background:var(--green);margin-right:3px;vertical-align:-0.5px}
.title{position:absolute;left:0;right:0;text-align:center;font-weight:700;font-size:17px}
.caption{position:absolute;left:0;right:0;text-align:center;font-size:7px;color:#444}
.btn{position:absolute;left:15px;width:205px;height:30px;background:var(--navy);color:var(--white);font-size:8px;letter-spacing:.3px;display:flex;align-items:center;justify-content:center}
.field{position:absolute;left:15px;width:202px;height:31px;border:1px solid #9fb0b8;font-size:8px;display:flex;align-items:center;padding:0 12px;justify-content:space-between}
.field.soft{border-color:var(--line);color:var(--muted)}
.chev{width:4px;height:4px;border-right:1px solid currentColor;border-top:1px solid currentColor;transform:rotate(45deg)}
.tile{position:absolute;width:85px;height:65px;border:1px solid #e3e3e3;display:flex;flex-direction:column;align-items:center;justify-content:flex-end;padding-bottom:6px;font-size:7px;gap:6px}
.tile.on{background:var(--green);border-color:var(--green);color:var(--white)}
.dots{position:absolute;left:0;right:0;text-align:center;font-size:6px;color:#bbb;letter-spacing:2px}
.side{position:absolute;font-size:11px;color:var(--ink)}
.opt{position:absolute;left:15px;width:192px;height:17px;border:1px solid var(--line);font-size:7.5px;display:flex;align-items:center;padding:0 8px;gap:6px}
.opt.on{background:var(--green);border-color:var(--green);color:var(--white);font-weight:700}
.opt .price{margin-left:auto;font-weight:700}
.info{position:absolute;left:215px;width:7px;height:7px;border-radius:50%;background:#ddd}
.dist{position:absolute;left:15px;width:192px;height:21px;border-bottom:1px solid #eee;font-size:7.5px;display:flex;align-items:center;gap:8px;padding-left:12px}
.dist b{width:20px;font-size:7px}
.dist b small{font-weight:400;font-size:5px}
.band{position:absolute;left:0;right:0;background:var(--band)}
.row{position:absolute;left:0;right:0;height:28px;border-bottom:1px solid #e6e6e6;display:flex;align-items:center;font-size:8px}
.row .x{width:27px;text-align:center;color:#aaa;font-size:8px}
.row .p{margin-left:auto;width:66px;text-align:center;font-weight:700;border-left:1px solid #e6e6e6;height:100%;display:flex;align-items:center;justify-content:center}
.slot{position:absolute;width:50px;height:24px;border:1px solid #e4e4e4;font-size:8px;display:flex;align-items:center;justify-content:center;color:#555}
.slot.on{background:var(--green);border-color:var(--green);color:var(--white);font-weight:500}
.ph::before{content:"";display:inline-block;width:5px;height:5px;border-radius:1px 50% 1px 50%;background:var(--green);margin-right:4px}
.pay{position:absolute;top:206px;height:21px;border:1px solid #ccc;font-size:7px;font-weight:700;color:var(--navy);display:flex;align-items:center;justify-content:center}
</style>
</head>
<body>

<!-- Screen 1: Start -->
<section class="screen" style="left:58px;top:34px">
  <div class="status"><span>●●●●● Netz</span><span>9:41 AM</span><span>100%<i class="bat"></i></span></div>
  <i class="back"></i>
  <svg class="basket" width="12" height="10" viewBox="0 0 12 10"><path d="M1 3h10l-1.5 6h-7z" fill="none" stroke="#1d1d1d" stroke-width="1.2"/></svg>
  <div class="abs" style="top:140px;left:0;right:0;text-align:center;font-size:21px;font-weight:500;color:var(--navy)"><span style="display:inline-block;width:14px;height:14px;border-radius:50%;background:var(--green);margin-right:6px;vertical-align:-1px"></span>Flickwerkzentrale</div>
  <div class="abs" style="top:359px;left:0;right:0;text-align:center;font-size:9.5px;color:var(--muted);letter-spacing:.4px;line-height:13px">DAS VERGLEICHSPORTAL FÜR<br>REPARATUREN IN DEINER NÄHE</div>
  <div class="band" style="bottom:0;height:12px;font-size:4px;color:#999;text-align:center;line-height:12px">Datenschutz</div>
</section>

<!-- Screen 2: Willkommen -->
<section class="screen" style="left:329px;top:34px">
  <div class="status"><span>●●●●● Netz</span><span>9:41 AM</span><span>100%<i class="bat"></i></span></div>
  <i class="back"></i>
  <svg class="basket" width="12" height="10" viewBox="0 0 12 10"><path d="M1 3h10l-1.5 6h-7z" fill="none" stroke="#1d1d1d" stroke-width="1.2"/></svg>
  <div class="brand">Flickwerkzentrale</div>
  <h1 class="title" style="top:84px">Herzlich willkommen!</h1>
  <p class="caption" style="top:114px">Bitte wählen Sie die Reparaturkategorie</p>
  <span class="side" style="left:16px;top:150px;color:#ccc">‹</span>
  <div class="tile on" style="left:27px;top:128px"><svg width="22" height="30" viewBox="0 0 22 30"><rect x="1.5" y="1.5" width="19" height="27" rx="3" fill="none" stroke="#fff" stroke-width="2"/></svg>Tablet</div>
  <div class="tile" style="left:120px;top:128px"><svg width="38" height="24" viewBox="0 0 38 24"><rect x="4" y="1" width="30" height="19" fill="none" stroke="#1d1d1d" stroke-width="1.5"/><path d="M0 22h38" stroke="#1d1d1d" stroke-width="1.5"/></svg>Laptop</div>
  <span class="side" style="left:212px;top:150px">›</span>
  <div class="dots" style="top:195px">• • • •</div>
  <div class="field soft" style="top:210px">Hersteller wählen<i class="chev"></i></div>
  <div class="field" style="top:248px">Verbindungs &amp; Anschlusselemente<i class="chev"></i></div>
  <div class="field" style="top:286px">Stadt / PLZ</div>
  <div class="field" style="top:323px">Strasse</div>
  <div class="btn" style="top:371px">LOS</div>
</section>

<!-- Screen 3: Vergleich -->
<section class="screen" style="left:603px;top:34px">
  <div class="status"><span>●●●●● Netz</span><span>9:41 AM</span><span>100%<i class="bat"></i></span></div>
  <i class="back"></i>
  <svg class="basket" width="12" height="10" viewBox="0 0 12 10"><path d="M1 3h10l-1.5 6h-7z" fill="none" stroke="#1d1d1d" stroke-width="1.2"/></svg>
  <div class="brand">Flickwerkzentrale</div>
  <p class="caption" style="top:61px">Hersteller wählen</p>
  <span class="side" style="left:14px;top:99px;color:#ccc">‹</span>
  <div class="tile on" style="left:27px;top:77px"><svg width="22" height="30" viewBox="0 0 22 30"><rect x="1.5" y="1.5" width="19" height="27" rx="3" fill="none" stroke="#fff" stroke-width="2"/></svg>Tablet Pro 12,9</div>
  <div class="tile" style="left:120px;top:77px"><svg width="22" height="30" viewBox="0 0 22 30"><rect x="1.5" y="1.5" width="19" height="27" rx="3" fill="none" stroke="#1d1d1d" stroke-width="2"/></svg>Tablet Pro 10,5</div>
  <span class="side" style="left:216px;top:99px">›</span>
  <div class="dots" style="top:144px">• • • • •</div>
  <div class="opt" style="top:160px">⌖ W-LAN Antenne<span class="price">50 €</span></div><i class="info" style="top:165px"></i>
  <div class="opt on" style="top:182px">✱ Bluetooth Antenne<span class="price">100 €</span></div><i class="info" style="top:187px"></i>
  <div class="opt" style="top:204px">≋ GPS Antenne<span class="price">120 €</span></div><i class="info" style="top:209px"></i>
  <div class="opt on" style="top:225px">⚒ SIM Lesemodul<span class="price">100 €</span></div><i class="info" style="top:230px"></i>
  <div class="abs" style="left:114px;top:249px;width:6px;height:6px;border-right:1.3px solid #1d1d1d;border-bottom:1.3px solid #1d1d1d;transform:rotate(45deg)"></div>
  <div class="abs" style="left:215px;top:270px;width:2px;height:20px;background:#1d1d1d"></div>
  <div class="dist" style="top:270px"><b>2 <small>km</small></b>Ahornallee 22, Berlin</div>
  <div class="dist" style="top:291px"><b>13 <small>km</small></b>Lindenweg 14, 80331 ...</div>
  <div class="dist" style="top:313px"><b>100 <small>m</small></b>Ahornallee 22, 10115 Berlin</div>
  <div class="dist" style="top:334px"><b>100 <small>m</small></b>Lindenweg 14, 80331 ...</div>
  <div class="btn" style="top:371px">LOS</div>
</section>

<!-- Screen 4: Werkstatt -->
<section class="screen" style="left:884px;top:34px">
  <div class="status"><span>●●●●● Netz</span><span>9:41 AM</span><span>100%<i class="bat"></i></span></div>
  <i class="back"></i>
  <svg class="basket" width="12" height="10" viewBox="0 0 12 10"><path d="M1 3h10l-1.5 6h-7z" fill="none" stroke="#1d1d1d" stroke-width="1.2"/></svg>
  <div class="brand">Flickwerkzentrale</div>
  <div class="abs" style="left:28px;top:82px;font-size:8px;font-weight:700;color:var(--green)">Geräteklinik.de</div>
  <div class="abs" style="left:184px;top:69px;width:28px;height:28px;border-radius:50%;background:#c9c9c9;border:2px solid #999"></div>
  <h2 class="abs" style="left:27px;top:110px;font-size:13.5px;line-height:16px;font-weight:700">Geräteklinik Berlin<br>Sicher Kaufen Garantie</h2>
  <div class="band" style="top:164px;height:49px;font-size:6.5px;color:#333">
    <div class="abs" style="left:27px;top:13px;line-height:12px">Lindenweg 14<br>80331 Musterstadt</div>
    <div class="abs" style="left:140px;top:13px;line-height:12px"><span class="ph">0123 - 4560 111</span><br><span class="ph">0123 - 4560 125</span></div>
  </div>
  <div class="abs" style="left:38px;top:222px;font-size:24px;font-weight:700">150<span style="font-size:13px;font-weight:500">m.</span></div>
  <div class="abs" style="left:40px;top:253px;font-size:9px;color:var(--green);letter-spacing:1px">★★★★<span style="color:#ccc">★</span></div>
  <div class="abs" style="left:125px;top:226px;width:1px;height:48px;background:#e5e5e5"></div>
  <svg class="abs" style="left:166px;top:228px" width="20" height="20" viewBox="0 0 20 20"><rect x="1" y="3" width="18" height="16" fill="none" stroke="#1d1d1d" stroke-width="1.5"/><path d="M1 7h18" stroke="#1d1d1d" stroke-width="2"/><text x="10" y="17" font-size="8" text-anchor="middle" font-family="Roboto,sans-serif" font-weight="700">19</text></svg>
  <div class="abs" style="left:152px;top:255px;font-size:5px;color:#6d7fc7">noch <b style="color:#1d1d1d;font-size:7px">3</b> Termin frei</div>
  <div class="band" style="top:280px;height:17px;font-size:6.5px;font-weight:700;padding-left:42px;line-height:17px">Ausgewählte Leistungen</div>
  <div class="row" style="top:297px"><span class="x">×</span>Bluetooth Antenne<span style="margin-left:auto;font-size:4.5px;color:#6d7fc7;margin-right:3px">200€ -50%</span><b style="margin-right:15px">100 €</b></div>
  <div class="row" style="top:325px"><span class="x">×</span>SIM Lesemodul<b style="margin-left:auto;margin-right:15px">100 €</b></div>
  <div class="btn" style="top:371px">JETZT ONLINE BESTPREIS BUCHEN</div>
</section>

<!-- Screen 5: Termine -->
<section class="screen" style="left:329px;top:515px">
  <div class="status"><span>●●●●● Netz</span><span>9:41 AM</span><span>100%<i class="bat"></i></span></div>
  <i class="back"></i>
  <svg class="basket" width="12" height="10" viewBox="0 0 12 10"><path d="M1 3h10l-1.5 6h-7z" fill="none" stroke="#1d1d1d" stroke-width="1.2"/></svg>
  <div class="brand">Flickwerkzentrale</div>
  <div class="abs" style="left:13px;top:69px;width:208px;height:279px;border:1px solid #e6e6e6;box-shadow:0 1px 4px rgba(0,0,0,.12);background:var(--white)">
    <h3 class="abs" style="left:15px;top:15px;font-size:13px;font-weight:700">Nächste Termine</h3>
    <span class="abs" style="right:12px;top:11px;font-size:14px;color:#bbb">×</span>
    <div class="abs" style="left:15px;top:52px;font-size:7px">AUG 17</div>
    <div class="slot on" style="left:15px;top:63px">11 AM</div>
    <div class="slot" style="left:75px;top:63px">1 PM</div>
    <div class="slot" style="left:135px;top:63px">3 PM</div>
    <div class="slot" style="left:15px;top:99px">4 PM</div>
    <div class="slot" style="left:75px;top:99px">11 AM</div>
    <div class="abs" style="left:15px;top:143px;font-size:7px">AUG 19</div>
    <div class="slot" style="left:15px;top:154px">10 AM</div>
    <div class="slot" style="left:75px;top:154px">11 AM</div>
    <div class="abs" style="left:15px;top:195px;font-size:7px;text-decoration:underline">SHOW CALENDAR</div>
    <div class="btn" style="left:13px;top:231px;width:180px">TERMIN BUCHEN</div>
  </div>
  <div class="btn" style="top:372px">JETZT ONLINE BESTPREIS BUCHEN</div>
</section>

<!-- Screen 6: Warenkorb -->
<section class="screen" style="left:603px;top:515px">
  <div class="status"><span>●●●●● Netz</span><span>9:41 AM</span><span>100%<i class="bat"></i></span></div>
  <i class="back"></i>
  <svg class="basket" width="12" height="10" viewBox="0 0 12 10"><path d="M1 3h10l-1.5 6h-7z" fill="none" stroke="#1d1d1d" stroke-width="1.2"/></svg>
  <div class="brand">Flickwerkzentrale</div>
  <h1 class="title" style="top:75px">Warenkorb</h1>
  <div class="band" style="top:105px;height:19px;font-size:6.5px;font-weight:700;display:flex;align-items:center"><span style="margin-left:38px">Leistung</span><span style="margin-left:auto;width:66px;text-align:center;border-left:1px solid #ddd">Preis</span></div>
  <div class="row" style="top:124px"><span class="x">×</span>Bluetooth Antenne<span class="p">100 €</span></div>
  <div class="row" style="top:152px"><span class="x">×</span>SIM Lesemodul<span class="p">100 €</span></div>
  <div class="band" style="top:180px;height:19px;font-size:7px;font-weight:700;display:flex;align-items:center"><span style="margin-left:27px">Total</span><span style="margin-left:auto;width:66px;text-align:center;border-left:1px solid #ddd">200 €</span></div>
  <div class="abs" style="left:27px;top:213px;font-size:7.5px;color:#444">Zahlungsmethoden:</div>
  <div class="pay" style="left:128px;width:35px">Karte</div>
  <div class="pay" style="left:168px;width:47px">Wallet Pay</div>
  <div class="btn" style="top:251px">ZUR KASSE</div>
  <p class="caption" style="top:304px">Passende Leistungen</p>
  <div class="opt" style="top:318px">⌖ W-LAN Antenne</div><i class="info" style="top:323px"></i>
  <div class="opt" style="top:339px">✱ Bluetooth Antenne</div><i class="info" style="top:344px"></i>
  <div class="opt" style="top:361px">≋ GPS Antenne</div><i class="info" style="top:366px"></i>
  <div class="opt" style="top:382px">⚒ SIM Lesemodul</div><i class="info" style="top:387px"></i>
</section>

<!-- Screen 7: Danke -->
<section class="screen" style="left:884px;top:515px">
  <div class="status"><span>●●●●● Netz</span><span>9:41 AM</span><span>100%<i class="bat"></i></span></div>
  <i class="back"></i>
  <svg class="basket" width="12" height="10" viewBox="0 0 12 10"><path d="M1 3h10l-1.5 6h-7z" fill="none" stroke="#1d1d1d" stroke-width="1.2"/></svg>
  <div class="brand">Flickwerkzentrale</div>
  <h1 class="title" style="top:75px">Vielen Dank!</h1>
  <div class="abs" style="left:0;right:0;top:122px;text-align:center;font-size:8px;font-weight:700;color:var(--green)">Geräteklinik.de</div>
  <div class="abs" style="left:0;right:0;top:149px;text-align:center;font-size:7px;line-height:12px">Lindenweg 14<br>80331 Musterstadt</div>
  <div class="abs" style="left:80px;top:181px;font-size:6.5px;line-height:14px"><span class="ph">0123 - 4560 111</span><br><span class="ph">0123 - 4560 125</span></div>
  <div class="abs" style="left:0;right:0;top:217px;text-align:center;font-size:7px;line-height:12px">Öffnungzeiten:<br>Mo-Fr. 9.00 Uhr - 18.00 Uhr<br>Sa. 10.00 Uhr - 15.00 Uhr</div>
  <div class="row" style="top:277px;border-top:1px solid #e6e6e6"><span class="x">×</span>Bluetooth Antenne<span class="p">100 €</span></div>
  <div class="row" style="top:306px"><span class="x">×</span>SIM Lesemodul<span class="p">100 €</span></div>
  <div class="abs" style="left:0;right:0;top:348px;text-align:center;font-size:7.5px">Total preis <b>200 €</b></div>
  <div class="btn" style="top:372px">BEZAHLEN</div>
</section>

</body>
</html>
```